Pinecrest Travel

We are new traveling company from Italy and looking for a really unique design as soon as possible of the main page.
Travel is an online business. We all do online research before taking a vacation. Since some of us will spend hours researching a trip before finally booking it on a travel website, design is critical.
People looking to travel are going to start with an idea. Some may be browsing for a specific type of trip (river cruise, kayaking, etc.) while others may be looking at specific dates (i.e. February). Still others are considering going to a specific destination such as the Grand Canyon, but all of these visitors are goal-oriented. This type of visitor is frustrated by not finding thle right information easily. This is why travel web design must offer several ways to navigate such as by date, location, activity, cost, etc.
The design should be easy to use for visitors, look fantastic and be easy to update and maintain.
Uploaded some sample pictures but feel free to use your own if it looks good. About colors, blue and white would mix great.

Our future address will be pinecresttravel-example.com

```html
<!DOCTYPE html>
<html lang="en">
<head>
<meta charset="utf-8">
<title>Pinecrest Travel</title>
<link href="https://fonts.googleapis.com/css2?family=Ubuntu:wght@400;500;700&family=Open+Sans:wght@400;600&display=swap" rel="stylesheet">
<style>
:root{
  --blue:#1ba6ea;
  --blue-deep:#128fd2;
  --blue-head:#1b8ed0;
  --navy:#0f5f94;
  --ink:#222;
  --muted:#8a8a8a;
  --white:#fff;
  --ph-sea:#3fbdd3;
  --ph-sky:#7fbfe0;
  --ph-grey:#8d9196;
  --ph-warm:#c4a890;
  --ph-dusk:#5a4c5c;
  --ph-room:#b8b2aa;
  --ph-gold:#b89a66;
}
*{box-sizing:border-box;margin:0;padding:0}
html,body{width:850px;height:1200px;overflow:hidden;background:var(--white)}
body{position:relative;font-family:"Open Sans",sans-serif;color:var(--ink)}
.abs{position:absolute}
.logo{left:78px;top:22px;font:700 18px "Ubuntu",sans-serif;color:var(--blue-deep)}
.contact-line{right:78px;display:flex;align-items:center;gap:6px;color:#333;white-space:nowrap}
.contact-line.phone{top:9px;font:500 14px "Ubuntu",sans-serif}
.contact-line.mail{top:35px;font-size:10.5px}
.main-nav{left:0;top:60px;width:850px;height:38px;background:linear-gradient(#1f1f1f,#000)}
.main-nav a{position:absolute;top:0;height:38px;line-height:38px;color:var(--white);font-size:12.5px;text-decoration:none}
.main-nav a.active{background:var(--blue);padding:0 13px}
.hero-band{left:0;top:98px;width:850px;height:312px;background:linear-gradient(var(--blue),var(--blue-deep))}
.slider{left:78px;top:110px;width:695px;height:287px;background:var(--white);padding:5px}
.slide-photo{width:100%;height:100%;background:var(--ph-sea)}
.caption{left:83px;top:234px;width:319px;height:46px;background:rgba(30,40,40,.55);color:var(--white);font:400 23px "Ubuntu",sans-serif;padding:6px 0 0 28px;white-space:nowrap}
.next{left:710px;top:239px}
.search-panel{left:78px;top:426px;width:695px;height:110px;background:linear-gradient(var(--blue),var(--blue-deep));border-radius:4px}
.search-title{left:93px;top:443px;font:700 14px "Ubuntu",sans-serif;color:var(--white)}
.field{top:476px;height:39px;background:var(--white);font-size:11px;color:#999;padding:12px 0 0 12px;white-space:nowrap}
.field .caret{position:absolute;right:10px;top:16px;width:0;height:0;border-left:5px solid transparent;border-right:5px solid transparent;border-top:7px solid #888}
.search-btn{left:678px;top:476px;width:84px;height:39px;background:linear-gradient(#176aa0,var(--navy));color:var(--white);font:700 13px "Ubuntu",sans-serif;text-align:center;line-height:39px}
.section-title{font:400 19px "Ubuntu",sans-serif;color:var(--blue-head);white-space:nowrap}
.col-title{font:400 14.5px "Ubuntu",sans-serif;color:var(--blue-head)}
.lead{left:77px;top:585px;font-size:12px;color:var(--ink);white-space:nowrap}
.body-text{font-size:10.6px;line-height:17.6px;color:var(--muted)}
.btn{height:30px;background:var(--blue);color:var(--white);font-size:11px;text-align:center;line-height:30px}
.ph{position:absolute}
.footer{left:0;top:1068px;width:850px;height:132px;background:linear-gradient(var(--blue),var(--blue-deep))}
.foot-nav a{position:absolute;top:1085px;color:var(--white);font-size:12.5px;text-decoration:none}
.social{top:1124px;width:23px;height:23px;background:linear-gradient(#fff,#ddd);border-radius:4px;border:1px solid #c8c8c8}
.copyright{left:0;top:1175px;width:850px;text-align:center;font-size:8.5px;color:var(--white)}
</style>
</head>
<body>
<header>
  <div class="abs logo">pinecresttravel</div>
  <div class="abs contact-line phone">
    <svg width="11" height="12" viewBox="0 0 24 24"><path fill="#333" d="M6.6 10.8c1.4 2.8 3.8 5.1 6.6 6.6l2.2-2.2c.3-.3.7-.4 1-.2 1.1.4 2.300.6 3.6.6.6 0 1 .4 1 1V20c0 .6-.4 1-1 1C10.6 21 3 13.4 3 4c0-.6.4-1 1-1h3.5c.6 0 1 .4 1 1 0 1.3.2 2.5.6 3.6.1.3 0 .7-.2 1z"/></svg>
    555- 010 246 810
  </div>
  <div class="abs contact-line mail">
    <svg width="12" height="9" viewBox="0 0 12 9"><rect width="12" height="9" fill="#333"/><path d="M0 0l6 5 6-5" stroke="#fff" fill="none"/></svg>
    info@pinecresttravel-example.com
  </div>
</header>

<nav class="abs main-nav">
  <a class="active" style="left:78px">Home</a>
  <a style="left:161px">About us</a>
  <a style="left:250px">Rates</a>
  <a style="left:318px">Location</a>
  <a style="left:402px">Reservations</a>
  <a style="left:510px">News &amp; Promos</a>
  <a style="left:635px">Contact</a>
</nav>

<section>
  <div class="abs hero-band"></div>
  <div class="abs slider"><div class="slide-photo" role="img" aria-label="Tropical lagoon with overwater bungalows, mountains and palm trees"></div></div>
  <div class="abs caption">Last minute winter escapes</div>
  <svg class="abs next" width="28" height="28" viewBox="0 0 28 28"><circle cx="14" cy="14" r="14" fill="#fff"/><path d="M10 9l5 5-5 5M14 9l5 5-5 5" stroke="#777" stroke-width="1.5" fill="none"/></svg>
</section>

<section>
  <div class="abs search-panel"></div>
  <div class="abs search-title">Advanced Search</div>
  <div class="abs field" style="left:93px;width:162px">Choose Your location<span class="caret"></span></div>
  <div class="abs field" style="left:263px;width:111px;padding-left:9px">Date</div>
  <div class="abs field" style="left:382px;width:131px">Enter Your activity</div>
  <div class="abs field" style="left:522px;width:146px">Choose Your Price<span class="caret"></span></div>
  <div class="abs search-btn">Search</div>
</section>

<section>
  <h1 class="abs section-title" style="left:77px;top:555px">Welcomt to pinecresttravel</h1>
  <p class="abs lead">Great panaromic mountain view makes the best place to admire nature.</p>
  <div class="ph" style="left:78px;top:619px;width:221px;height:150px;background:var(--ph-sea)" role="img" aria-label="Thatched overwater bungalows"></div>
  <p class="abs body-text" style="left:313px;top:614px;width:166px">Lorem ipsum dolor sit amet, con-sectetur adipisicing elit, sed do eiusmod tempor incididunt ut labore et dolore magna aliqua. Ut enim ad minim veniam, quis nos-trud exercitation ullamco laboris nisi ut aliquip ex ea commodo consequat.</p>

  <h2 class="abs section-title" style="left:490px;top:557px">Recent Photogallery</h2>
  <div class="ph" style="left:491px;top:593px;width:89px;height:61px;background:var(--ph-sky)" role="img" aria-label="Beach signpost and luggage"></div>
  <div class="ph" style="left:587px;top:593px;width:89px;height:61px;background:var(--ph-grey)" role="img" aria-label="Travel agency counter"></div>
  <div class="ph" style="left:683px;top:593px;width:89px;height:61px;background:var(--ph-grey)" role="img" aria-label="Shop interior"></div>
  <div class="ph" style="left:491px;top:667px;width:89px;height:62px;background:var(--ph-warm)" role="img" aria-label="Couple relaxing on the beach"></div>
  <div class="ph" style="left:587px;top:667px;width:89px;height:62px;background:var(--ph-sky)" role="img" aria-label="Man in sunglasses on holiday"></div>
  <div class="ph" style="left:683px;top:667px;width:89px;height:62px;background:var(--ph-warm)" role="img" aria-label="Couple on a tropical holiday"></div>
  <div class="abs btn" style="left:491px;top:745px;width:45px">More</div>
</section>

<section>
  <h3 class="abs col-title" style="left:77px;top:804px">Our Offers</h3>
  <h3 class="abs col-title" style="left:315px;top:804px">Our accommodations</h3>
  <h3 class="abs col-title" style="left:552px;top:804px">Our tours</h3>
  <div class="ph" style="left:78px;top:837px;width:221px;height:96px;background:var(--ph-dusk)" role="img" aria-label="Outdoor lounge chair with candles"></div>
  <div class="ph" style="left:314px;top:837px;width:222px;height:96px;background:var(--ph-room)" role="img" aria-label="Bright hotel room with round table"></div>
  <div class="ph" style="left:551px;top:837px;width:222px;height:96px;background:var(--ph-gold)" role="img" aria-label="Hotel bedroom with lamps"></div>
  <p class="abs body-text" style="left:78px;top:943px;width:225px">Lorem ipsum dolor sit amet, consectetur adipisicing elit, sed do eiusmod tempor incid-idunt ut labore et dolore magna aliqua.</p>
  <p class="abs body-text" style="left:314px;top:943px;width:225px">Lorem ipsum dolor sit amet, consectetur adipisicing elit, sed do eiusmod tempor incid-idunt ut labore et dolore magna aliqua.</p>
  <p class="abs body-text" style="left:551px;top:943px;width:225px">Lorem ipsum dolor sit amet, consectetur adipisicing elit, sed do eiusmod tempor incid-idunt ut labore et dolore magna aliqua.</p>
  <div class="abs btn" style="left:78px;top:1007px;width:71px;height:35px;line-height:35px">Read More</div>
  <div class="abs btn" style="left:314px;top:1007px;width:71px;height:35px;line-height:35px">Read More</div>
  <div class="abs btn" style="left:550px;top:1007px;width:71px;height:35px;line-height:35px">Read More</div>
</section>

<footer>
  <div class="abs footer"></div>
  <nav class="foot-nav">
    <a style="left:131px">Home</a>
    <a style="left:202px">About us</a>
    <a style="left:291px">Rates</a>
    <a style="left:358px">Location</a>
    <a style="left:442px">Reservations</a>
    <a style="left:550px">News &amp; Promos</a>
    <a style="left:675px">Contact</a>
  </nav>
  <div class="abs social" style="left:363px"></div>
  <div class="abs social" style="left:389px"></div>
  <div class="abs social" style="left:414px"></div>
  <div class="abs social" style="left:440px"></div>
  <div class="abs social" style="left:465px"></div>
  <p class="abs copyright">Copyright © 2014 pinecresttravel-example.com. All rights reserved.</p>
</footer>
</body>
</html>
```